We are a recruitment company based in Norwich/Cambridge England.
I have included our company logo which we want to remain the same.

What we are looking for is a new creative Business card which will really stand out!!

Contact Information for Business Card

Harriet Dunmore
email: Harriet@plavex.co.uk
Address: Brackwell House
Fenmoor Enterprise Park
Partridge Way
Norwich
QB9 3KX
Tel:01632 960418

```html
<!DOCTYPE html>
<html lang="en">
<head>
<meta charset="utf-8">
<title>Plavex Business Card</title>
<link rel="stylesheet" href="https://fonts.googleapis.com/css2?family=Jost:wght@400;500&family=Open+Sans:wght@600;700&display=swap">
<style>
  :root {
    --backdrop: #2a2a2b;
    --card: #1f1f20;
    --card-edge: #262627;
    --map-tone: #2b2b2c;
    --grey-text: #8d8d90;
    --light-text: #e6e6e6;
    --brand-green: #7dc42c;
    --rule: #8a8a8d;
  }
  * { box-sizing: border-box; margin: 0; padding: 0; }
  html, body {
    width: 1200px;
    height: 900px;
    overflow: hidden;
    background: radial-gradient(ellipse at 60% 30%, #3a3a3b 0%, var(--backdrop) 70%);
    font-family: "Jost", sans-serif;
  }
  .sheet {
    position: relative;
    width: 1200px;
    height: 900px;
  }
  .card {
    position: absolute;
    left: 250px;
    width: 700px;
    height: 400px;
    background: linear-gradient(160deg, var(--card-edge), var(--card));
    box-shadow: 0 14px 30px rgba(0,0,0,0.45);
    overflow: hidden;
  }
  .card--front { top: 30px; }
  .card--back { top: 470px; }

  /* Front */
  .world-map {
    position: absolute;
    inset: 20px 40px 60px 40px;
    background: radial-gradient(ellipse at 50% 45%, var(--map-tone) 0%, rgba(43,43,44,0.4) 55%, transparent 80%);
  }
  .brand {
    position: absolute;
    display: flex;
    flex-direction: column;
  }
  .brand__row { display: flex; align-items: center; gap: 14px; }
  .brand__mark {
    width: 52px; height: 52px; border-radius: 50%;
  }
  .brand__name {
    font-weight: 500;
    line-height: 1;
  }
  .brand__tagline {
    font-size: 9px;
    letter-spacing: 3.2px;
    margin-top: 4px;
  }
  .card--front .brand { left: 50%; top: 140px; transform: translateX(-50%); }
  .card--front .brand__mark { background: #161617; box-shadow: inset 0 0 0 2px #2e2e2f; }
  .card--front .brand__name { font-size: 56px; color: #c9c9cb; }
  .card--front .brand__tagline { color: #9a9a9c; padding-left: 66px; }
  .front-url {
    position: absolute;
    left: 0; right: 0; bottom: 46px;
    text-align: center;
    font-size: 15px;
    letter-spacing: 3px;
    color: var(--light-text);
  }
  .front-url .accent { color: var(--brand-green); }

  /* Back */
  .card--back .brand { right: 44px; top: 50px; align-items: flex-end; }
  .card--back .brand__mark { width: 40px; height: 40px; background: var(--brand-green); }
  .card--back .brand__name { font-size: 44px; color: var(--brand-green); }
  .card--back .brand__tagline { color: var(--grey-text); font-size: 8px; letter-spacing: 2.6px; }
  .holder {
    position: absolute;
    left: 60px; top: 150px;
  }
  .holder__name {
    font-family: "Open Sans", sans-serif;
    font-weight: 700;
    font-size: 40px;
    color: var(--grey-text);
    line-height: 1.1;
  }
  .holder__role {
    font-family: "Open Sans", sans-serif;
    font-weight: 600;
    font-size: 20px;
    color: var(--brand-green);
    margin-top: 2px;
  }
  .divider {
    position: absolute;
    left: 60px; right: 60px; top: 245px;
    height: 2px;
    background: var(--rule);
  }
  .contacts {
    position: absolute;
    left: 60px; top: 262px;
    list-style: none;
  }
  .contacts li {
    display: flex; align-items: center; gap: 12px;
    font-size: 17px;
    color: var(--light-text);
    line-height: 26px;
  }
  .contacts svg { width: 18px; height: 18px; flex: none; }
  .contacts .accent { color: var(--brand-green); }
  .address {
    position: absolute;
    right: 60px; bottom: 36px;
    text-align: right;
    font-size: 17px;
    line-height: 26px;
    color: var(--light-text);
  }
</style>
</head>
<body>
<main class="sheet">
  <section class="card card--front">
    <div class="world-map" role="img" aria-label="Faint world map spanning the card background"></div>
    <div class="brand">
      <div class="brand__row">
        <span class="brand__mark"></span>
        <span class="brand__name">Plavex</span>
      </div>
      <span class="brand__tagline">Technology Recruitment</span>
    </div>
    <p class="front-url">www.<span class="accent">plavex</span>.co.uk</p>
  </section>

  <section class="card card--back">
    <div class="brand">
      <div class="brand__row">
        <span class="brand__mark"></span>
        <span class="brand__name">Plavex</span>
      </div>
      <span class="brand__tagline">Technology Recruitment</span>
    </div>

    <div class="holder">
      <h1 class="holder__name">Harriet Dunmore</h1>
      <p class="holder__role">CEO &amp; FOUNDER</p>
    </div>

    <div class="divider"></div>

    <ul class="contacts">
      <li>
        <svg viewBox="0 0 24 24" aria-hidden="true"><path fill="#7dc42c" d="M6.6 10.8a15.1 15.1 0 0 0 6.6 6.6l2.2-2.2c.3-.3.7-.4 1-.2 1.1.4 2.3.6 3.6.6.6 0 1 .4 1 1V20c0 .6-.4 1-1 1A17 17 0 0 1 3 4c0-.6.4-1 1-1h3.5c.6 0 1 .4 1 1 0 1.3.2 2.5.6 3.6.1.3 0 .7-.2 1z"/></svg>
        01632 960418
      </li>
      <li>
        <svg viewBox="0 0 24 24" aria-hidden="true"><rect x="2" y="5" width="20" height="14" rx="1.5" fill="#7dc42c"/><path d="M2.5 6l9.5 7 9.5-7" fill="none" stroke="#1f1f20" stroke-width="1.6"/></svg>
        Harriet@plavex.co.uk
      </li>
      <li>
        <svg viewBox="0 0 24 24" aria-hidden="true"><circle cx="13" cy="10" r="6.5" fill="none" stroke="#7dc42c" stroke-width="2.4"/><path d="M8.5 14.5L3 20" stroke="#7dc42c" stroke-width="2.8" stroke-linecap="round"/></svg>
        <span>www.<span class="accent">plavex</span>.co.uk</span>
      </li>
    </ul>

    <address class="address" style="font-style: normal;">
      Brackwell House Fenmoor Enterprise Park,<br>
      Partridge Way Norwich, QB9 3KX
    </address>
  </section>
</main>
</body>
</html>
```